Web Design for guards MMJ transport and security services

Harbor Crest Protective solutions a tallow unified company, is looking for a designer to create a website that displays our service portfolio. We need marketing pictures and content to be created in a original and competitive fashion, intriguing to our customers. We will need forms on the website to be created for calendar booking (somehow integrate into exchange if possible) and general inquiry forms. There will need to be pages dedicated to our staff, MMJ trasnport & Courier services, our vehicles, alarm systems, video systems, video monitoring, private investigations, and surveillance aduit and compliance investigations, payment gateway integration, and general company information. I Have attached our main company logo. Also have a emphasis on being state licensed by the Colorado RPB. Have a link to our parent site, tallowcctv.example

Target Market(s)

Colorado Marijuana industry, MMJ transport services, guard services, armed gaurd services.

Contact Information for Business Card

Would like a sleek simple design highlighting what we offer. must match the website and have a overall professional straight to the point appearance.

Number of Pages Required

1 page

Colors
33b8a4
00a990
9bcb3c
acd036
cadf82
85cae6
33a6d7
0792cd

Requirements
Must have
• Easy to use, lots of images, professional.
Nice to have
• Creativity

```html
<!DOCTYPE html>
<html lang="en">
<head>
<meta charset="utf-8">
<title>Harbor Crest Protective Solutions</title>
<link href="https://fonts.googleapis.com/css2?family=Open+Sans:wght@400;600;700&family=Roboto:wght@400;500;700&display=swap" rel="stylesheet">
<style>
:root{
  --teal:#00a990;
  --teal-soft:#33b8a4;
  --teal-deep:#008a75;
  --green:#9bcb3c;
  --blue:#0792cd;
  --ink:#333a3f;
  --muted:#7a8288;
  --line:#dfe3e5;
  --pale:#f3f5f6;
  --white:#ffffff;
}
*{box-sizing:border-box;margin:0;padding:0}
html,body{width:1200px;height:2644px;overflow:hidden}
body{font-family:"Open Sans",sans-serif;color:var(--ink);background:var(--white);font-size:14px}
.canvas{width:1200px;height:2644px;position:relative}

/* header */
.site-header{height:112px;padding:0 60px;display:flex;justify-content:space-between;align-items:flex-start;background:var(--white)}
.brand{display:flex;align-items:center;gap:10px;margin-top:26px}
.brand-mark{width:40px;height:40px;border-radius:50%;background:var(--teal)}
.brand-name{font-family:"Roboto",sans-serif;font-weight:700;font-size:20px;color:var(--ink);line-height:1.1}
.header-right{display:flex;flex-direction:column;align-items:flex-end;gap:14px;padding-top:12px}
.contact-row{display:flex;align-items:center;gap:8px;font-size:12px;color:var(--muted)}
.contact-row .dot{width:16px;height:16px;border-radius:50%;background:var(--teal)}
.main-nav{display:flex;gap:4px}
.main-nav a{font-family:"Roboto",sans-serif;font-size:12px;font-weight:500;color:var(--ink);text-decoration:none;padding:10px 14px;border-bottom:3px solid transparent}
.main-nav a.active{border-bottom-color:var(--teal);color:var(--teal)}

.service-strip{height:40px;background:var(--teal);display:flex;justify-content:center;align-items:center;gap:0}
.service-strip a{color:var(--white);text-decoration:none;font-size:12px;padding:0 20px;border-right:1px solid rgba(255,255,255,.35);line-height:18px}
.service-strip a:last-child{border-right:0}

/* hero */
.hero{height:608px;position:relative;background:linear-gradient(180deg,#2d6f96 0%,#5c8fb0 40%,#c88a4c 75%,#3a2f35 100%)}
.hero-copy{position:absolute;left:0;right:0;top:300px;text-align:center;color:var(--white)}
.hero-title{font-family:"Roboto",sans-serif;font-size:54px;font-weight:500;letter-spacing:1px}
.hero-sub{font-size:15px;margin-top:10px;line-height:1.5}
.hero-dots{position:absolute;bottom:22px;left:0;right:0;display:flex;justify-content:center;gap:8px}
.hero-dots span{width:10px;height:10px;border-radius:50%;background:rgba(255,255,255,.5)}
.hero-dots span.on{background:var(--white)}

/* welcome */
.welcome{height:260px;background:var(--teal-soft);color:var(--white);text-align:center;padding-top:40px}
.section-title{font-family:"Roboto",sans-serif;font-size:28px;font-weight:500;letter-spacing:.5px}
.welcome p{width:900px;margin:20px auto 0;font-size:12px;line-height:1.7}
.btn{display:inline-block;font-family:"Roboto",sans-serif;font-size:11px;font-weight:700;letter-spacing:.5px;padding:9px 22px;text-decoration:none;border-radius:2px}
.btn-dark{background:var(--teal-deep);color:var(--white);margin-top:20px}
.btn-teal{background:var(--teal);color:var(--white)}
.btn-outline{border:1px solid var(--teal);color:var(--teal)}

/* services */
.services{height:550px;padding-top:50px;text-align:center}
.title-rule{display:flex;align-items:center;justify-content:center;gap:20px}
.title-rule::before,.title-rule::after{content:"";width:90px;height:1px;background:var(--line)}
.services .section-title{color:var(--ink)}
.service-grid{display:grid;grid-template-columns:340px 300px 340px;justify-content:center;gap:20px;margin-top:50px;align-items:center}
.service-col{display:flex;flex-direction:column;gap:60px}
.service-item{display:flex;align-items:center;gap:18px}
.service-col.left .service-item{flex-direction:row-reverse;text-align:right}
.service-col.right .service-item{text-align:left}
.service-icon{flex:none;width:64px;height:64px;border-radius:50%;background:var(--blue);display:flex;align-items:center;justify-content:center}
.service-item h3{font-family:"Roboto",sans-serif;font-size:15px;font-weight:700;color:var(--ink)}
.service-item p{font-size:12px;color:var(--muted);line-height:1.5;margin-top:4px}
.service-item .more{font-size:10px;font-weight:700;color:var(--teal)}
.center-badge{width:240px;height:240px;margin:0 auto;border-radius:50%;border:2px solid var(--line);display:flex;align-items:center;justify-content:center;gap:10px}
.center-badge .brand-mark{width:30px;height:30px}
.services .btn-outline{margin-top:56px}

/* security */
.security{height:320px;background:var(--pale);display:flex;gap:40px;padding:40px 60px}
.security-photo{width:520px;height:240px;background:linear-gradient(135deg,#6f7d3a,#b9a55a 55%,#5d6b34)}
.security-copy h2{font-family:"Roboto",sans-serif;font-size:22px;font-weight:700;color:var(--ink)}
.security-copy p{font-size:12px;color:var(--muted);line-height:1.7;margin-top:14px}
.security-copy .btn{margin-top:18px}

/* testimonials */
.testimonials{height:320px;text-align:center;padding-top:44px;position:relative}
.testimonials .section-title{color:var(--ink)}
.quote{width:820px;margin:34px auto 0;position:relative;font-size:14px;color:var(--muted);line-height:1.7}
.quote-mark{position:absolute;top:-18px;font-family:Georgia,serif;font-size:64px;color:#c4cacd;line-height:1}
.quote-mark.open{left:-60px}
.quote-mark.close{right:-60px;top:30px}
.author{display:flex;align-items:center;justify-content:center;gap:14px;margin-top:22px;font-size:11px;font-weight:700;color:var(--ink)}
.author::before,.author::after{content:"";width:50px;height:1px;background:var(--line)}
.slider-dots{display:flex;justify-content:center;gap:8px;margin-top:18px}
.slider-dots span{width:10px;height:10px;border-radius:50%;border:1px solid var(--teal)}
.slider-dots span.on{background:var(--teal)}

/* footer */
.site-footer{height:400px;background:var(--teal);color:var(--white);display:grid;grid-template-columns:230px 260px 300px 200px;gap:40px;padding:50px 60px 0}
.footer-brand{display:flex;flex-direction:column;gap:20px}
.footer-brand .name{display:flex;align-items:center;gap:10px;font-family:"Roboto",sans-serif;font-weight:700;font-size:22px}
.footer-brand .name span{width:26px;height:26px;border-radius:50%;background:var(--white)}
.partner-seal{width:90px;height:90px;border-radius:50%;background:#e9d27a;border:4px solid var(--white)}
.site-footer h4{font-family:"Roboto",sans-serif;font-size:20px;font-weight:500;margin-bottom:18px}
.contact-list{list-style:none;display:flex;flex-direction:column;gap:12px;font-size:12px}
.contact-list li{display:flex;align-items:flex-start;gap:10px}
.contact-list svg{flex:none;margin-top:2px}
.newsletter p{font-size:12px;line-height:1.6}
.signup{display:flex;margin-top:16px}
.signup .field{width:180px;height:34px;background:var(--white);color:var(--muted);font-size:11px;padding:10px}
.signup .btn{background:var(--green);color:var(--white);height:34px;border-radius:0}
.follow p{font-size:12px;line-height:1.6}
.social{display:flex;gap:10px;margin-top:16px}
.social span{width:30px;height:30px;border-radius:50%;border:1.5px solid var(--white)}
.copyright{height:34px;background:var(--teal-deep);color:var(--white);font-size:11px;display:flex;align-items:center;justify-content:center}
</style>
</head>
<body>
<div class="canvas">

<header class="site-header">
  <div class="brand">
    <span class="brand-mark"></span>
    <span class="brand-name">Harbor Crest</span>
  </div>
  <div class="header-right">
    <div class="contact-row">Call Us : 720-555-0148 &nbsp;|&nbsp; Follow Us : <span class="dot"></span><span class="dot"></span><span class="dot"></span></div>
    <nav class="main-nav">
      <a class="active" href="#">HOME</a>
      <a href="#">ABOUT US</a>
      <a href="#">OUR EFFORTS</a>
      <a href="#">OUR VEHICLES</a>
      <a href="#">CONTACT US</a>
    </nav>
  </div>
</header>

<nav class="service-strip">
  <a href="#">MMJ transport &amp; Courier services</a>
  <a href="#">Alarm systems</a>
  <a href="#">Video systems</a>
  <a href="#">Video monitoring</a>
  <a href="#">Security investigations</a>
  <a href="#">Surveillance audit</a>
  <a href="#">Compliance investigations</a>
</nav>

<section class="hero" role="img" aria-label="Security camera mounted over a city skyline at dusk">
  <div class="hero-copy">
    <h1 class="hero-title">TRANSPORT &amp; SECURITY SERVICES</h1>
    <p class="hero-sub">Reliable and licensed protection that lets you focus on your business, your people,<br>and your assets, backed by a team that keeps every route safe and secure.</p>
  </div>
  <div class="hero-dots"><span class="on"></span><span></span><span></span></div>
</section>

<section class="welcome">
  <h2 class="section-title">WELCOME TO HARBOR CREST</h2>
  <p>We are a state licensed protective firm serving the Colorado cannabis industry with secure transport, guard, alarm and video services. Our trained staff work with every client to plan safe routes, watch key sites and keep each shipment and facility compliant with state rules. We pair modern tools with hands on service so that owners and managers always know their people, product and property are in good hands, day and night, across the whole state.</p>
  <a class="btn btn-dark" href="#">READ MORE</a>
</section>

<section class="services">
  <h2 class="section-title title-rule">OUR SERVICES</h2>
  <div class="service-grid">
    <div class="service-col left">
      <div class="service-item">
        <span class="service-icon"><svg width="30" height="30" viewBox="0 0 30 30" fill="none" stroke="#fff" stroke-width="2"><rect x="3" y="9" width="16" height="11"/><path d="M19 13h5l3 4v3h-8z"/><circle cx="8" cy="22" r="2.5"/><circle cx="22" cy="22" r="2.5"/></svg></span>
        <div><h3>COURIER SERVICES</h3><p>Secure licensed transport for product and<br>cash between your sites each day.</p><span class="more">READ MORE</span></div>
      </div>
      <div class="service-item">
        <span class="service-icon"><svg width="30" height="30" viewBox="0 0 30 30" fill="none" stroke="#fff" stroke-width="2"><path d="M8 20v-7a7 7 0 0 1 14 0v7"/><path d="M5 20h20"/><path d="M13 24h4"/></svg></span>
        <div><h3>ALARM SYSTEMS</h3><p>Monitored alarms that alert our team the<br>moment anything looks out of place.</p><span class="more">READ MORE</span></div>
      </div>
    </div>
    <div class="center-badge">
      <span class="brand-mark"></span><span class="brand-name">Harbor Crest</span>
    </div>
    <div class="service-col right">
      <div class="service-item">
        <span class="service-icon"><svg width="30" height="30" viewBox="0 0 30 30" fill="none" stroke="#fff" stroke-width="2"><path d="M4 18l3-7h16l3 7v4H4z"/><circle cx="9" cy="22" r="2.5"/><circle cx="21" cy="22" r="2.5"/></svg></span>
        <div><h3>OUR VEHICLES</h3><p>Armored and tracked vehicles built for<br>safe and discreet deliveries.</p><span class="more">READ MORE</span></div>
      </div>
      <div class="service-item">
        <span class="service-icon"><svg width="30" height="30" viewBox="0 0 30 30" fill="none" stroke="#fff" stroke-width="2"><rect x="4" y="9" width="15" height="12" rx="1"/><path d="M19 13l7-3v10l-7-3z"/></svg></span>
        <div><h3>VIDEO SYSTEMS</h3><p>Camera systems with live viewing and<br>recorded footage kept for review.</p><span class="more">READ MORE</span></div>
      </div>
    </div>
  </div>
  <a class="btn btn-outline" href="#">VIEW MORE SERVICES</a>
</section>

<section class="security">
  <div class="security-photo" role="img" aria-label="Entrance sign of the state cannabis licensing office"></div>
  <div class="security-copy">
    <h2>SECURITY &amp; SURVEILLANCE</h2>
    <p>We design, install and manage a full range of security and surveillance systems for cannabis growers, retail stores and transport hubs. Every plan is built around state rules so that your site passes each audit with confidence and your staff feel safe at work.</p>
    <p>Our licensed team checks cameras, alarms and access points on a set schedule, reviews footage and reports any gaps. We also run compliance audits and quiet investigations when a problem needs a closer look, giving owners clear answers and simple next steps.</p>
    <a class="btn btn-teal" href="#">READ MORE</a>
  </div>
</section>

<section class="testimonials">
  <h2 class="section-title title-rule">WHAT OTHERS SAY</h2>
  <div class="quote">
    <span class="quote-mark open">&ldquo;</span>
    <p>Harbor Crest has handled our deliveries and site security for two years now. Their guards are on time, their reports are clear, and every state inspection since has gone smoothly. We trust them with our people and our product, and we would not change a thing about the service.</p>
    <span class="quote-mark close">&rdquo;</span>
  </div>
  <div class="author">WARREN ELLERY</div>
  <div class="slider-dots"><span class="on"></span><span></span><span></span></div>
</section>

<footer class="site-footer">
  <div class="footer-brand">
    <div class="name"><span></span>TALLOW</div>
    <div class="partner-seal"></div>
  </div>
  <div>
    <h4>Contact Us</h4>
    <ul class="contact-list">
      <li><svg width="14" height="14" viewBox="0 0 14 14" fill="#fff"><path d="M3 1l2 3-1.2 1.2a8 8 0 0 0 5 5L10 9l3 2-1 2.5C6 13 1 8 .5 2z"/></svg>720-555-0148 (Phone)</li>
      <li><svg width="14" height="14" viewBox="0 0 14 14" fill="#fff"><path d="M3 1l2 3-1.2 1.2a8 8 0 0 0 5 5L10 9l3 2-1 2.5C6 13 1 8 .5 2z"/></svg>720-555-0162 (Fax)</li>
      <li><svg width="14" height="14" viewBox="0 0 14 14" fill="none" stroke="#fff" stroke-width="1.4"><rect x="1" y="3" width="12" height="8"/><path d="M1 3l6 5 6-5"/></svg>info@tallowcctv.example</li>
      <li><svg width="14" height="14" viewBox="0 0 14 14" fill="#fff"><path d="M7 0a5 5 0 0 1 5 5c0 4-5 9-5 9S2 9 2 5a5 5 0 0 1 5-5zm0 3a2 2 0 1 0 0 4 2 2 0 0 0 0-4z"/></svg>4120 Quarry Lane,<br>Denver, CO 80216</li>
    </ul>
  </div>
  <div class="newsletter">
    <h4>Newsletter Signup</h4>
    <p>Register your email address to get<br>the latest news and offers from us.</p>
    <div class="signup"><span class="field">Email Address</span><a class="btn" href="#">SUBSCRIBE</a></div>
  </div>
  <div class="follow">
    <h4>Follow Us</h4>
    <p>Stay in touch with our team and see the latest updates from the field.</p>
    <div class="social"><span></span><span></span><span></span><span></span></div>
  </div>
</footer>
<div class="copyright">© Copyright 2016 - Harbor Crest Protective solutions. All Rights Reserved.</div>

</div>
</body>
</html>
```